Teeth Whitening Clinic Website Redesign - Social Proof Theme

NEW TEETH SITEREVAMP CURRENT WEBSITE:WWW.SANDIEGOSTEETHWHITENING.COMTHEME:SOCIAL PROOF/5 STAR REVIEWS/TESTIMONIALS THEME:https://maps.example.net/QxRvPLoKzN84 I want a testimonial themed, social proof themed website so customers will be sold by testimonials all over the website….I like a nice clean simple site but with all important factors standing out like CALLS TO ACTIONS, for example the $99 special link in header on original design. Also, testimonials throughout the website placed methodically as not to be FORCED and CLUTTEREDKeep all same exact content for all pages and elements of current design. All buttons, calls to action, navigation, etc. Please do not leave anything out from current design. SPECIAL INSTRUCTIONS for banner image:I want to use actual customer photos inside the banner image in a way that really pops and grabs attention. Please grab some customer photos from my PG Account, fk or rateway account: Also, I want to integrate 5 star rateway logo, friendbook review 5 stars icon, searchly business page 5 stars icon, etc. on the banner as well to show social proof as much as possible. Actual customer photos to be used throughout website:https://www.photogram.example/brightharborsmilestudioplace/ https://www.friendbook.com/SDTeethWhitening/https://www.reviewhub.example/biz/bright-harbor-smile-studio-place-bright-harbor-5 Reviews:https://www.reviewhub.example/biz/bright-harbor-smile-studio-place-bright-harbor-5 https://www.friendbook.com/pg/SDTeethWhitening/reviews/?ref=page_internalhttps://goo.gl/maps/TmJcABLAJwC2 Please do home page first to come up with theme then after approval home page we can move forward additional pages.

Target Market(s)

PEOPLE THAT CARE ABOUT DENTAL HYGEINE AND OR CARE ABOUT THEIR TEETH SMILE

Industry/Entity Type

Dental Clinic

Number of Pages Required

5+ page

Colors

Designer to choose colors to be used in the design.

Requirements
Must have
• NEW TEETH SITE
• REVAMP CURRENT WEBSITE:
• WWW.BRIGHTHARBORSMILESTUDIO.EXAMPLE
• THEME:
• SOCIAL PROOF/5 STAR REVIEWS/TESTIMONIALS THEME:
• https://maps.example.net/QxRvPLoKzN84
• I want a testimonial themed, social proof themed website so customers will be sold by testimonials all over the website….I like a nice clean simple site but with all important factors standing out like CALLS TO ACTIONS, for example the $99 special link in header on original design. Also, testimonials throughout the website placed methodically as not to be FORCED and CLUTTERED
• Keep all same exact content for all pages and elements of current design. All buttons, calls to action, navigation, etc. Please do not leave anything out from current design.
• SPECIAL INSTRUCTIONS for banner image:
• I want to use actual customer photos inside the banner image in a way that really pops and grabs attention. Please grab some customer photos from my PG Account, fk or rateway account:
• Also, I want to integrate 5 star rateway logo, friendbook review 5 stars icon, searchly business page 5 stars icon, etc. on the banner as well to show social proof as much as possible.
• Actual customer photos to be used throughout website:
• https://www.photogram.example/brightharborsmilestudioplace/
• https://www.friendbook.example/BHSmileStudio/
• https://www.reviewhub.example/biz/bright-harbor-smile-studio-place-bright-harbor-5
• Reviews:
• https://www.friendbook.example/pg/BHSmileStudio/reviews/?ref=page_internal
• Please do home page first to come up with theme then after approval home page we can move forward additional pages.
Nice to have
• NEW TEETH SITE
• REVAMP CURRENT WEBSITE:
• THEME:
• Reviews:
Should not have
• NEW TEETH SITE
• REVAMP CURRENT WEBSITE:
• THEME:
• Reviews:

```html
<!DOCTYPE html>
<html lang="en">
<head>
<meta charset="utf-8">
<title>Bright Harbor Smile Studio</title>
<link href="https://fonts.googleapis.com/css2?family=Raleway:wght@300;400;500;600;700&family=Lato:wght@400;700&display=swap" rel="stylesheet">
<style>
:root{
  --blue:#16a6cc;
  --blue-light:#5fc6df;
  --dark:#3b3b3b;
  --ink:#333;
  --grey:#8a8a8a;
  --soft:#f3f3f3;
  --white:#fff;
}
*{box-sizing:border-box;margin:0;padding:0}
html,body{width:1200px;height:4290px;overflow:hidden}
body{font-family:"Raleway",sans-serif;color:var(--ink);background:var(--white);position:relative}
.abs{position:absolute}
/* header */
.site-header{position:absolute;left:0;top:0;width:1200px;height:103px;background:#fff}
.brand{position:absolute;left:108px;top:22px;display:flex;align-items:center;gap:10px}
.brand-dot{width:52px;height:52px;border-radius:50%;background:#d9ecf2}
.brand-name{font-size:23px;font-weight:500;color:var(--grey);line-height:1}
.contact-chip{position:absolute;top:28px;display:flex;gap:12px;align-items:flex-start}
.chip-box{width:46px;height:46px;background:var(--blue);display:flex;align-items:center;justify-content:center}
.chip-text{font-size:14.5px;line-height:27px;color:#444;margin-top:-4px}
.main-nav{position:absolute;left:0;top:103px;width:1200px;height:85px;background:var(--blue);display:flex;justify-content:center;align-items:center;gap:29px;color:#fff;font-size:15.5px}
/* hero */
.hero{position:absolute;left:0;top:188px;width:1200px;height:636px;overflow:hidden}
.hero-photo{position:absolute;inset:0;background:linear-gradient(100deg,#4a5560,#6d7a86 30%,#3f4c58 55%,#6a7480 80%,#444f5a)}
.hero-shade{position:absolute;inset:0;background:rgba(20,30,40,.35)}
.hero h1{position:absolute;top:172px;width:100%;text-align:center;color:#fff;font-size:36px;font-weight:300;letter-spacing:.5px}
.hero h1 b{font-weight:700}
.hero-sub{position:absolute;top:232px;width:100%;text-align:center;color:#fff;font-size:22px;font-weight:500;line-height:45px}
.btn-ghost{position:absolute;top:340px;width:213px;height:52px;border:3px solid #fff;border-radius:26px;color:#fff;font-weight:700;font-size:17px;display:flex;align-items:center;justify-content:center;gap:8px}
.rating{position:absolute;top:460px;color:#fff;text-align:center}
.rating-name{font-size:36px;font-weight:500;display:flex;align-items:center;gap:8px;justify-content:center}
.rating-name i{width:22px;height:22px;border-radius:50%;background:#fff;display:inline-block}
.stars{font-size:16px;letter-spacing:2px;margin-top:2px}
.slide-arrow{position:absolute;width:34px;height:34px;border:2px solid #fff;border-radius:50%}
/* sections */
h2.sec{position:absolute;width:100%;text-align:center;font-size:34px;font-weight:400;color:#444}
h2.sec b{font-weight:600;color:var(--blue)}
.btn-outline{position:absolute;height:47px;border:3px solid #444;border-radius:24px;font-size:15.5px;font-weight:500;display:flex;align-items:center;justify-content:center;gap:8px;color:#333;box-shadow:0 2px 4px rgba(0,0,0,.2)}
.body-copy{position:absolute;font-family:"Lato",sans-serif;font-size:15px;line-height:31.6px;color:#444}
/* compare */
.plan{position:absolute;top:3358px;width:227px;height:352px;background:var(--soft);text-align:center}
.plan-head{height:77px;background:var(--blue);color:#fff;font-size:27px;font-weight:600;display:flex;align-items:center;justify-content:center}
.plan-row{height:45px;border-bottom:1px dashed #aaa;font-size:15px;display:flex;align-items:center;justify-content:center;margin:0 0}
.plan.ours{background:var(--dark);color:#fff;box-shadow:0 0 6px rgba(0,0,0,.3)}
.plan.ours .plan-head{background:#fff;color:var(--grey);font-size:22px;font-weight:500;gap:8px}
.plan.ours .plan-row{border-bottom:1px dashed #999}
.plan-spacer{height:28px}
/* footer */
.site-footer{position:absolute;left:0;top:3796px;width:1200px;height:494px;background:var(--dark);color:#fff}
.foot-icon{position:absolute;top:133px;width:84px;height:84px;border-radius:50%;background:var(--blue);display:flex;align-items:center;justify-content:center}
.foot-info{position:absolute;top:230px;width:340px;text-align:center;font-size:17.5px;line-height:28px}
.foot-links{position:absolute;width:100%;text-align:center;font-size:15.5px}
.social{position:absolute;top:428px;width:32px;height:32px;border:2px solid #fff;border-radius:50%}
</style>
</head>
<body>

<header class="site-header">
  <div class="brand"><span class="brand-dot"></span><span class="brand-name">Bright Harbor Smile Studio</span></div>
  <div class="contact-chip" style="left:533px">
    <div class="chip-box"><svg width="20" height="26" viewBox="0 0 20 26"><path d="M10 0a9 9 0 0 0-9 9c0 7 9 17 9 17s9-10 9-17a9 9 0 0 0-9-9z" fill="#fff"/><circle cx="10" cy="9" r="3.5" fill="#16a6cc"/></svg></div>
    <div class="chip-text">2840 Harborview Rd. #205<br>Bright Harbor, CA 92100</div>
  </div>
  <div class="contact-chip" style="left:816px">
    <div class="chip-box" style="color:#fff;font-size:26px;font-weight:700">$</div>
    <div class="chip-text">Click Here to Get Our $99 Teeth<br>Whiting Deal (Reg: $378)</div>
  </div>
</header>

<nav class="main-nav">
  <svg width="16" height="14" viewBox="0 0 16 14"><path d="M8 0 0 7h2v7h4V9h4v5h4V7h2z" fill="#fff"/></svg>
  <span>Our Process</span><span>Photos</span><span>Free Treatments</span><span>Testimonials</span><span>Blog</span><span>FAQ</span><span>Contact</span><span>Gift Certificates</span><span>Book Appointment</span>
</nav>

<section class="hero">
  <div class="hero-photo" role="img" aria-label="Collage of smiling clinic customers holding review signs"></div>
  <div class="hero-shade"></div>
  <h1>GET THAT WHITE SMILE <b>YOU'VE ALWAYS WANTED</b></h1>
  <p class="hero-sub">Amazing Results, The Most Effective System, More Affordable<br>Than The Dentist</p>
  <div class="btn-ghost" style="left:375px"><svg width="12" height="16" viewBox="0 0 12 16"><path d="M1 0v14l4-4 3 6 2-1-3-6h5z" fill="#fff"/></svg>BOOK ONLINE</div>
  <div class="btn-ghost" style="left:611px"><svg width="16" height="16" viewBox="0 0 16 16"><path d="M16 0 0 7l7 2 2 7z" fill="#fff"/></svg>CONTACT US</div>
  <div class="slide-arrow" style="left:53px;top:245px"><svg width="30" height="30" viewBox="0 0 30 30"><path d="M18 8l-7 7 7 7" stroke="#fff" stroke-width="2.5" fill="none"/></svg></div>
  <div class="slide-arrow" style="left:1113px;top:245px"><svg width="30" height="30" viewBox="0 0 30 30"><path d="M12 8l7 7-7 7" stroke="#fff" stroke-width="2.5" fill="none"/></svg></div>
  <div class="rating" style="left:140px;width:180px"><div class="rating-name"><i></i>Rateway</div><div class="stars">★★★★★</div></div>
  <div class="rating" style="left:480px;width:240px"><div class="rating-name"><i></i>Friendbook</div><div class="stars">★★★★★</div></div>
  <div class="rating" style="left:850px;width:190px"><div class="rating-name"><i></i>Searchly</div><div class="stars">★★★★★</div></div>
  <svg class="abs" style="left:0;top:520px" width="1200" height="116" viewBox="0 0 1200 116">
    <path d="M0 0 C300 95 900 95 1200 0 L1200 116 L0 116Z" fill="#fff"/>
    <path d="M0 8 C320 110 880 110 1200 8" stroke="#cfd6db" stroke-width="8" fill="none"/>
    <path d="M0 0 C300 95 900 95 1200 0" stroke="#16a6cc" stroke-width="5" fill="none"/>
  </svg>
</section>

<section class="about">
  <div class="abs" style="left:78px;top:952px;width:160px;height:160px;border-radius:50%;background:var(--blue-light)"></div>
  <div class="abs" style="left:130px;top:1125px;width:140px;height:140px;border-radius:50%;background:#8e8e8e"></div>
  <div class="abs" role="img" aria-label="Happy customers holding smile signs in the clinic" style="left:149px;top:925px;width:324px;height:324px;border-radius:50%;background:radial-gradient(circle at 40% 40%,#8a8f94,#4d5257);border:4px solid #fff"></div>
  <svg class="abs" style="left:289px;top:1065px" width="44" height="44" viewBox="0 0 44 44"><circle cx="22" cy="22" r="20" fill="#fff"/><path d="M17 13l13 9-13 9z" fill="#333"/></svg>
  <div class="abs" style="left:540px;top:918px;font-size:34px;line-height:45px;color:var(--blue);font-weight:300">BRIGHT HARBOR SMILE <b style="color:#333;font-weight:600">STUDIO</b></div>
  <div class="abs" style="left:540px;top:1011px;font-size:22px;color:var(--blue);font-weight:500">The best price, service and results.</div>
  <p class="body-copy" style="left:540px;top:1046px;width:590px">Bright Harbor Smile Studio features state-of-the-art technologies that are safe, industry-unique and very cost-effective. Our teeth whitening system utilizes the latest blue light whitening technology. Our Blue Light Systems are calibrated precisely for optimal activation of our exclusive hydrogen peroxide based whitening solution which is manufactured in a FDA registered facility in the USA.</p>
  <div class="btn-outline" style="left:540px;top:1215px;width:249px"><svg width="14" height="14" viewBox="0 0 14 14"><rect x="1" y="2" width="12" height="11" fill="none" stroke="#333" stroke-width="1.5"/><path d="M1 5h12" stroke="#333" stroke-width="1.5"/></svg>Schedule Appointment</div>
</section>

<section class="how">
  <svg class="abs" style="left:0;top:1355px" width="1200" height="580" viewBox="0 0 1200 580">
    <path d="M0 40 C400 -10 900 -10 1200 0 L1200 575 C800 560 300 560 0 520Z" fill="#bdbdbd"/>
    <path d="M0 30 C400 10 900 10 1200 30 L1200 555 C800 540 300 540 0 535Z" fill="#16a6cc"/>
  </svg>
  <div class="abs" role="img" aria-label="Faded photo of customers celebrating" style="left:0;top:1385px;width:1200px;height:520px;background:radial-gradient(ellipse at 55% 50%,rgba(255,255,255,.16),rgba(255,255,255,0) 70%)"></div>
  <h2 class="sec" style="top:1448px;color:#fff;font-weight:300">HOW IT <b style="color:#fff">WORKS</b></h2>
  <p class="body-copy" style="left:175px;top:1509px;width:850px;text-align:center;color:#fff;font-family:Raleway,sans-serif;font-size:15.5px">We have a very effective teeth whitening treatment that is guaranteed to get you quick results in about 1 hour. To start the treatment you'll apply a Hydrogen Peroxide based whitening agent to your teeth. We then place our cold blue light directly in front of your exposed teeth for 15 minutes per treatment. The lighting systems we use activate the whitening agent and thats what accelerates the whitening process, giving you whiter teeth in less than an hour.<br>We always perform what we call a "Triple Treatment". So that's 3 of the 15 minute treatments all done consecutively, in the same visit. The actual whitening time is a total of 45 minutes. Now there is a few minute break in between each 15 minute treatment and this is why we tell all of our patients to give yourself one hour at the office.</p>
  <div class="btn-outline" style="left:518px;top:1808px;width:166px;border-color:#fff;color:#fff;font-weight:700;box-shadow:none"><svg width="12" height="15" viewBox="0 0 12 15"><path d="M0 0h8l4 4v11H0z" fill="#fff"/></svg>Read More</div>
</section>

<section class="why">
  <h2 class="sec" style="top:2023px;font-weight:300">WHY <b>CHOOSE US</b></h2>
  <svg class="abs" style="left:103px;top:2110px" width="420" height="420" viewBox="0 0 420 420">
    <circle cx="210" cy="209" r="200" fill="none" stroke="#999" stroke-width="1.5"/>
    <path d="M308 35 A200 200 0 0 1 410 209" fill="none" stroke="#16a6cc" stroke-width="2"/>
    <circle cx="115" cy="30" r="9" fill="#444"/><circle cx="308" cy="35" r="10" fill="#16a6cc"/>
    <circle cx="10" cy="209" r="9" fill="#444"/><circle cx="410" cy="209" r="9" fill="#444"/>
    <circle cx="115" cy="388" r="9" fill="#444"/><circle cx="308" cy="388" r="9" fill="#444"/>
  </svg>
  <div class="abs" role="img" aria-label="Staff members smiling together" style="left:146px;top:2152px;width:334px;height:334px;border-radius:50%;background:radial-gradient(circle at 50% 45%,#9a9da1,#555a5f)"></div>
  <div class="abs" style="left:146px;top:2250px;width:334px;text-align:center;color:#fff;font-size:54px;font-weight:700;line-height:60px">$<br>PRICE</div>
  <div class="abs" style="left:591px;top:2146px;font-size:33px;color:var(--blue);font-weight:500">$&nbsp; PRICE</div>
  <p class="body-copy" style="left:591px;top:2198px;width:480px">Sed ut perspiciatis unde omnis iste natus error sit voluptatem accusantium doloremque laudantium, totam rem aperiam, eaque ipsa quae ab illo inventore veritatis et quasi architecto beatae vitae dicta sunt explicabo. Nemo enim ipsam voluptatem quia voluptas sit aspernatur aut odit aut fugit, sed quia consequuntur magni dolores eos qui ratione voluptatem sequi nesciunt.</p>
  <div class="btn-outline" style="left:591px;top:2439px;width:170px"><svg width="12" height="15" viewBox="0 0 12 15"><path d="M0 0h8l4 4v11H0z" fill="#333"/></svg>Read More</div>
</section>

<section class="testimonials">
  <div class="abs" role="img" aria-label="Customer photos from the clinic, faded" style="left:0;top:2622px;width:1200px;height:570px;background:linear-gradient(90deg,#5c6670,#7b858e 40%,#66707a 70%,#4f5963)"></div>
  <svg class="abs" style="left:0;top:2615px" width="1200" height="590" viewBox="0 0 1200 590">
    <path d="M0 0H1200V40C900 0 400 0 0 55Z" fill="#fff"/>
    <path d="M900 8 C1020 10 1120 25 1200 45 L1200 85 C1100 50 1000 20 900 8Z" fill="#a9e0ee"/>
    <path d="M0 500 C400 560 800 560 1200 520 L1200 590 L0 590Z" fill="#fff"/>
    <path d="M0 500 C400 560 800 560 1200 520 L1200 545 C800 585 400 585 0 525Z" fill="#16a6cc"/>
  </svg>
  <h2 class="sec" style="top:2758px;color:#fff;font-weight:700">TESTIMONIALS</h2>
  <div class="abs" style="left:261px;top:2850px;width:677px;height:207px;border:2px solid rgba(255,255,255,.8);background:rgba(255,255,255,.08)"></div>
  <p class="abs" style="left:294px;top:2890px;width:600px;color:#fff;font-size:15.5px;line-height:27px">I also appreciated that they took the time to explain all the instructions and didn't mind me asking addition l questions about the take home kit and aftercare instructions.</p>
  <div class="abs" role="img" aria-label="Reviewer avatar" style="left:298px;top:2994px;width:66px;height:66px;border-radius:50%;background:#e2c8a8;border:2px solid #fff"></div>
  <div class="abs" style="left:383px;top:3017px;color:#fff;font-size:16px;font-weight:600">Marcus T.</div>
  <svg class="abs" style="left:20px;top:2910px" width="30" height="40" viewBox="0 0 30 40"><path d="M22 4L8 20l14 16" stroke="#fff" stroke-width="4" fill="none"/></svg>
  <svg class="abs" style="left:1150px;top:2910px" width="30" height="40" viewBox="0 0 30 40"><path d="M8 4l14 16L8 36" stroke="#fff" stroke-width="4" fill="none"/></svg>
</section>

<section class="compare">
  <h2 class="sec" style="top:3266px"><b>COMPARE</b> US</h2>
  <div class="plan" style="left:88px"><div class="plan-head">LAMP PRO</div><div class="plan-spacer"></div><div class="plan-row">Hours 1-2</div><div class="plan-row">Difficult / Dentist</div><div class="plan-row">$600 - $300</div><div class="plan-row">Limited Availability</div><div class="plan-row" style="border:0">Pain &amp; Sensitivity</div></div>
  <div class="plan ours" style="left:355px"><div class="plan-head"><span style="width:34px;height:34px;border-radius:50%;background:#d9ecf2;display:inline-block"></span><span style="font-size:17px;line-height:20px;text-align:left">Bright Harbor<br>Smile Studio</span></div><div class="plan-spacer"></div><div class="plan-row">Mins 45</div><div class="plan-row">Very Easy</div><div class="plan-row">$378</div><div class="plan-row">Appt Only</div><div class="plan-row" style="border:0">No Pain</div></div>
  <div class="plan" style="left:619px"><div class="plan-head">QUICKGLOW</div><div class="plan-spacer"></div><div class="plan-row">Days 7-14</div><div class="plan-row">Difficult / Dentist</div><div class="plan-row">$600 - $300</div><div class="plan-row">Limited Availability</div><div class="plan-row" style="border:0">Sensitivity</div></div>
  <div class="plan" style="left:884px"><div class="plan-head">HOME KITS</div><div class="plan-spacer"></div><div class="plan-row">Days 7-30</div><div class="plan-row">Difficult</div><div class="plan-row">$150 - $50</div><div class="plan-row">Store Purchase</div><div class="plan-row" style="border:0">Sensitivity</div></div>
  <svg class="abs" style="left:20px;top:3510px" width="30" height="44" viewBox="0 0 30 44"><path d="M22 4L8 22l14 18" stroke="#16a6cc" stroke-width="4" fill="none"/></svg>
  <svg class="abs" style="left:1150px;top:3510px" width="30" height="44" viewBox="0 0 30 44"><path d="M8 4l14 18L8 40" stroke="#16a6cc" stroke-width="4" fill="none"/></svg>
</section>

<footer class="site-footer">
  <svg class="abs" style="left:0;top:-10px" width="1200" height="110" viewBox="0 0 1200 110">
    <path d="M0 0H1200V90C900 -5 300 -5 0 100Z" fill="#fff"/>
    <path d="M0 100 C300 20 900 20 1200 85" stroke="#16a6cc" stroke-width="4" fill="none"/>
  </svg>
  <div class="foot-icon" style="left:256px"><svg width="40" height="44" viewBox="0 0 40 44"><path d="M20 2a12 12 0 0 0-12 12c0 10 12 22 12 22s12-12 12-22A12 12 0 0 0 20 2z" fill="none" stroke="#fff" stroke-width="2"/><circle cx="20" cy="14" r="4" fill="none" stroke="#fff" stroke-width="2"/><path d="M6 36h28l4 6H2z" fill="none" stroke="#fff" stroke-width="2"/></svg></div>
  <div class="foot-icon" style="left:559px"><svg width="40" height="40" viewBox="0 0 40 40"><path d="M10 4l7 8-4 4c2 5 6 9 11 11l4-4 8 7-4 6C18 34 6 22 4 8z" fill="none" stroke="#fff" stroke-width="2"/></svg></div>
  <div class="foot-icon" style="left:864px"><svg width="44" height="32" viewBox="0 0 44 32"><rect x="2" y="2" width="40" height="28" fill="none" stroke="#fff" stroke-width="2"/><path d="M2 2l20 16L42 2M2 30l15-14M42 30L27 16" fill="none" stroke="#fff" stroke-width="2"/></svg></div>
  <div class="foot-info" style="left:128px">2840 Harborview Rd. #205<br>Bright Harbor, CA 92100</div>
  <div class="foot-info" style="left:431px">Phone: 1-555-260-0149<br>Fax:&nbsp; 1-555-260-0149</div>
  <div class="foot-info" style="left:736px">Email: info@brightharbor.example<br>Email: info@brightharbor.example</div>
  <div class="foot-links" style="top:306px">Home &nbsp;|&nbsp; Book Appointment Online &nbsp;|&nbsp; Our Process &nbsp;|&nbsp; Photos &nbsp;|&nbsp; Testimonials &nbsp;|&nbsp; Blog &nbsp;|&nbsp; FAQ &nbsp;|&nbsp; Contact &nbsp;|&nbsp; Gift Certificates</div>
  <div class="foot-links" style="top:348px">After Care &nbsp;|&nbsp; Consent Form Espanol &nbsp;|&nbsp; Consent Form English &nbsp;|&nbsp; Cancellation Policy &nbsp;|&nbsp; Privacy Policy &nbsp;|&nbsp; Free Treatments</div>
  <div class="foot-links" style="top:396px;font-size:17px">© 2018 Company Name &nbsp;All right reserved</div>
  <span class="social" style="left:529px"></span><span class="social" style="left:566px"></span><span class="social" style="left:602px"></span><span class="social" style="left:639px"></span>
</footer>

</body>
</html>
```